Web Developer Needs a Business Card Design

I need a personal business card design that represents me as a web developer for potential employers. I would like the background to be a dark color on the front for contrast with my logo and name. The back will have all my information along with a smaller version of the logo. I want something with a modern look and feel, not too conservative. This will be used for potential employers and freelance work.

Industry/Entity Type

Business

Contact Information for Business Card

Front should have my logo and name. The back should have all my personal information which would include: name: Tom Varulek, phone: 570-614-3098, email: tomvarulek@quillbox.net, website url: www.tomvarulek.net, logo, web developer.

Font styles to use
Sans Serif

Requirements
Must have
• Must include my logo. The color palette base color will be the logo color.

```html
<!DOCTYPE html>
<html lang="en">
<head>
<meta charset="utf-8">
<title>Tom Varulek – Business Card</title>
<link rel="stylesheet" href="https://fonts.googleapis.com/css2?family=Open+Sans:wght@400;600;700&display=swap">
<style>
  :root {
    --teal: #6ec8b4;
    --teal-light: #b3e3d9;
    --ink: #111111;
    --rule: #6f6f6f;
    --paper: #ffffff;
    --backdrop: #e9e5e2;
  }
  * { margin: 0; padding: 0; box-sizing: border-box; }
  html, body {
    width: 1200px; height: 900px; overflow: hidden;
    background: var(--backdrop);
    font-family: "Open Sans", sans-serif;
    color: var(--ink);
  }
  .card {
    position: absolute; left: 280px;
    width: 640px; height: 366px;
    background: var(--paper);
    box-shadow: 0 6px 18px rgba(0,0,0,.18);
    overflow: hidden;
  }
  .card--front { top: 48px; }
  .card--back { top: 486px; }

  .brand-mark {
    position: absolute; left: 0; right: 0;
    display: flex; align-items: center; justify-content: center; gap: 12px;
    color: var(--teal); font-weight: 700;
  }
  .brand-mark__dot {
    border-radius: 50%; background: var(--teal);
  }
  .card--front .brand-mark { top: 112px; font-size: 34px; }
  .card--front .brand-mark__dot { width: 30px; height: 30px; }
  .card--back .brand-mark { top: 52px; font-size: 26px; }
  .card--back .brand-mark__dot { width: 22px; height: 22px; }

  .front-name {
    position: absolute; top: 206px; left: 0; right: 0;
    text-align: center; font-size: 30px; font-weight: 600;
  }

  .back-art { position: absolute; inset: 0; }

  .back-title {
    position: absolute; top: 184px; left: 0; right: 0;
    text-align: center; line-height: 1.05;
  }
  .back-title__name { font-size: 36px; font-weight: 400; }
  .back-title__role { font-size: 19px; font-weight: 700; }

  .contact {
    position: absolute; top: 268px; left: 0; right: 0;
    text-align: center; font-size: 20px; font-weight: 600; line-height: 1.2;
    list-style: none;
  }
</style>
</head>
<body>

<section class="card card--front" aria-label="Business card front">
  <div class="brand-mark"><span class="brand-mark__dot"></span><span>Tom Varulek</span></div>
  <p class="front-name">Tom Varulek</p>
</section>

<section class="card card--back" aria-label="Business card back">
  <svg class="back-art" viewBox="0 0 640 366" width="640" height="366" aria-hidden="true">
    <polygon points="0,168 48,196 570,168 640,128 640,366 0,366" fill="var(--teal-light)"/>
    <polygon points="190,182 470,170 470,366 190,366" fill="var(--teal)"/>
    <polyline points="0,162 48,190 570,162 640,122" fill="none" stroke="var(--teal)" stroke-width="6"/>
    <polyline points="0,176 48,204 570,176 640,136" fill="none" stroke="var(--paper)" stroke-width="5"/>
    <line x1="0" y1="262" x2="640" y2="246" stroke="var(--rule)" stroke-width="2"/>
    <line x1="120" y1="250" x2="210" y2="247" stroke="var(--ink)" stroke-width="2.5"/>
    <line x1="440" y1="233" x2="540" y2="230" stroke="var(--ink)" stroke-width="2.5"/>
  </svg>
  <div class="brand-mark"><span class="brand-mark__dot"></span><span>Tom Varulek</span></div>
  <div class="back-title">
    <p class="back-title__name">Tom Varulek</p>
    <p class="back-title__role">web developer</p>
  </div>
  <ul class="contact">
    <li>570-614-3098</li>
    <li>tomvarulek@quillbox.net</li>
    <li>www.tomvarulek.net</li>
  </ul>
</section>

</body>
</html>
```